Business Cards for a law firm

Business cards for our law firm. Use our silhoette logo and OAK PARTNERS - check our website (www.oakpartners.example)

Contact Information for Business Card

our silhouette logo, OAK PARTNERS, 800-555-0147, Dorian Pemberton, dorian@oakpartners.example

Requirements
Must have
• our silhouette logo, OAK PARTNERS, 800-555-0147, Dorian Pemberton, dorian@oakpartners.example

```html
<!DOCTYPE html>
<html lang="en">
<head>
<meta charset="utf-8">
<title>Oak Partners – Business Cards</title>
<link rel="stylesheet" href="https://fonts.googleapis.com/css2?family=Montserrat:wght@400;500;700&display=swap">
<style>
  :root {
    --navy: #233369;
    --white: #ffffff;
    --backdrop: #dde3e5;
    --logo-font: "Montserrat", sans-serif;
  }
  * { box-sizing: border-box; margin: 0; padding: 0; }
  html, body {
    width: 1200px;
    height: 960px;
    overflow: hidden;
    background: var(--backdrop);
    font-family: var(--logo-font);
  }
  .card {
    position: absolute;
    left: 247px;
    width: 705px;
    height: 403px;
    overflow: hidden;
  }
  .card--front { top: 58px; background: var(--navy); color: var(--white); }
  .card--back { top: 500px; background: var(--white); color: var(--navy); }

  .brand-mark {
    position: absolute;
    background: currentColor;
  }
  .brand-name {
    position: absolute;
    font-weight: 400;
    line-height: 1;
    text-transform: uppercase;
    white-space: nowrap;
  }
  .brand-name span { display: block; }

  .card--front .brand-mark { left: 118px; top: 162px; width: 78px; height: 78px; }
  .card--front .brand-name { left: 226px; top: 142px; font-size: 52px; letter-spacing: 1px; }
  .card--front .brand-name span + span { margin-top: 4px; }

  .card--back .brand-mark { left: 30px; top: 170px; width: 52px; height: 52px; }
  .card--back .brand-name { left: 100px; top: 165px; font-size: 33px; letter-spacing: 0.5px; }
  .card--back .brand-name span + span { margin-top: 2px; }

  .divider {
    position: absolute;
    left: 349px;
    top: 101px;
    width: 2px;
    height: 199px;
    background: var(--navy);
  }
  .person-name {
    position: absolute;
    left: 375px;
    top: 136px;
    font-size: 24px;
    letter-spacing: 1px;
    text-transform: uppercase;
    white-space: nowrap;
  }
  .person-name .first { font-weight: 700; }
  .person-name .last { font-weight: 400; }

  .contact-list {
    position: absolute;
    left: 375px;
    top: 196px;
    list-style: none;
  }
  .contact-item {
    display: flex;
    align-items: center;
    height: 21px;
    font-size: 13px;
    font-weight: 500;
    letter-spacing: 1px;
    text-transform: uppercase;
    white-space: nowrap;
  }
  .contact-item--phone { font-size: 16px; height: 24px; }
  .contact-icon { width: 15px; height: 15px; margin-right: 11px; flex: none; }

  .footer-band {
    position: absolute;
    top: 354px;
    height: 26px;
    background: var(--navy);
  }
  .footer-band--left { left: 0; width: 328px; }
  .footer-band--right { left: 372px; right: 0; }
  .footer-mark {
    position: absolute;
    left: 340px;
    top: 355px;
    width: 20px;
    height: 20px;
    background: var(--navy);
  }
</style>
</head>
<body>

<section class="card card--front" aria-label="Card front">
  <div class="brand-mark"></div>
  <div class="brand-name"><span>Oak</span><span>Partners</span></div>
</section>

<section class="card card--back" aria-label="Card back">
  <div class="brand-mark"></div>
  <div class="brand-name"><span>Oak</span><span>Partners</span></div>

  <div class="divider"></div>

  <h1 class="person-name"><span class="first">Dorian</span> <span class="last">Pemberton</span></h1>

  <ul class="contact-list">
    <li class="contact-item contact-item--phone">
      <svg class="contact-icon" viewBox="0 0 16 16" aria-hidden="true">
        <path fill="currentColor" d="M3.2 1.5l2.2-.4 1.3 3-1.4 1.1c.7 1.6 2 2.9 3.5 3.6l1.1-1.4 3 1.3-.4 2.2c-.2.8-.9 1.2-1.7 1.1C5.7 11.3 2.4 8 1.8 3.2c-.1-.8.4-1.5 1.4-1.7z"/>
        <path fill="none" stroke="currentColor" stroke-width="1.2" d="M9.5 2.5a4 4 0 0 1 4 4M9.5 4.8a1.7 1.7 0 0 1 1.7 1.7"/>
      </svg>
      800-555-0147
    </li>
    <li class="contact-item">
      <svg class="contact-icon" viewBox="0 0 16 16" aria-hidden="true">
        <circle cx="8" cy="8" r="6.8" fill="none" stroke="currentColor" stroke-width="1.6"/>
        <ellipse cx="8" cy="8" rx="3" ry="6.8" fill="none" stroke="currentColor" stroke-width="1.2"/>
        <path d="M1.5 8h13" stroke="currentColor" stroke-width="1.2"/>
      </svg>
      www.oakpartners.example
    </li>
    <li class="contact-item">
      <svg class="contact-icon" viewBox="0 0 16 16" aria-hidden="true">
        <rect x="1" y="5" width="14" height="10" fill="none" stroke="currentColor" stroke-width="1.4"/>
        <path d="M1 5l7 5 7-5" fill="none" stroke="currentColor" stroke-width="1.4"/>
        <circle cx="8" cy="4" r="2.5" fill="none" stroke="currentColor" stroke-width="1.2"/>
      </svg>
      dorian@oakpartners.example
    </li>
  </ul>

  <div class="footer-band footer-band--left"></div>
  <div class="footer-band footer-band--right"></div>
  <div class="footer-mark"></div>
</section>

</body>
</html>
```